I am looking to create a newly designed website for our national leadership conference which is entitled, "The Harbor of Momentum Leadership Summit". The Harbor of Momentum Leadership Summit is a national conference for student leaders that prepares them for career leadership success. The current website can be seen at www.harborofmomentumleadershipsummit.com.

My goal for the new site is to create a more updated, fresh, hip, and exciting look that appeals to the younger generation while also maintaining are professional appeal. The color should be black, white, and gold. We want there to be live videos played and places to insert pictures for the panels as well.

I look forward to seeing you the new creations.

Requirements
Must have
• Ability to play videos on the home page and throughout the website. Also, make sure that the website shows up clearly on an zTablet.
Nice to have
• Nice look

```html
<!DOCTYPE html>
<html lang="en">
<head>
<meta charset="utf-8">
<title>Harbor of Momentum – Conference</title>
<link href="https://fonts.googleapis.com/css2?family=Roboto:wght@300;400;500;700&display=swap" rel="stylesheet">
<style>
:root{
  --gold:#b8913f;
  --gold-light:#d2ad5e;
  --ink:#222222;
  --text:#444444;
  --muted:#777777;
  --nav-top:#333333;
  --nav-bottom:#151515;
  --footer:#2f2f2f;
  --footer-text:#9a9a9a;
  --pill-bg:#ececec;
  --line:#d8d8d8;
}
*{box-sizing:border-box;margin:0;padding:0}
html,body{width:1177px;height:1200px;overflow:hidden;background:#fff}
body{font-family:"Roboto",sans-serif;color:var(--text);position:relative}
.wrap{position:absolute;left:73px;right:72px}

/* header */
.site-header{height:122px;position:relative}
.follow{position:absolute;left:73px;top:47px;display:flex;align-items:center;gap:4px;font-size:12px;font-weight:500;color:var(--ink)}
.follow span{margin-right:4px}
.social{width:29px;height:29px;display:block}
.social.s1{background:#3b5998}.social.s2{background:#2aa3d9}.social.s3{background:#0e76a8}.social.s4{background:#d41f1f}.social.s5{background:#8d7b63}
.brand{position:absolute;left:0;right:0;top:18px;text-align:center}
.brand-mark{width:60px;height:60px;border-radius:50%;background:linear-gradient(150deg,var(--gold-light),var(--gold));margin:0 auto 8px}
.brand-name{font-size:16px;font-weight:700;letter-spacing:1.5px;color:#3a2f28}
.cta{position:absolute;right:72px;top:34px;width:219px;height:51px;border-radius:26px;background:linear-gradient(180deg,var(--gold-light),var(--gold));color:#fff;font-size:22px;font-weight:500;display:flex;align-items:center;justify-content:center;letter-spacing:.5px}

/* main nav */
.main-nav{height:60px;background:linear-gradient(180deg,var(--nav-top),var(--nav-bottom));display:flex;justify-content:center}
.main-nav a{color:#fff;text-decoration:none;font-size:14px;font-weight:500;letter-spacing:.4px;display:flex;align-items:center;padding:0 22px;height:60px}
.main-nav a.active{background:linear-gradient(180deg,var(--gold-light),var(--gold));padding:0 19px}

/* breadcrumb & title */
.breadcrumb{top:214px;font-size:12px;font-weight:500;color:var(--muted);letter-spacing:.3px;padding-left:8px}
.breadcrumb .current{color:var(--gold)}
.rule{top:249px;height:1px;background:var(--line)}
.page-title{top:273px;font-size:33px;font-weight:400;color:var(--ink);letter-spacing:.4px}

/* sub nav */
.sub-nav{top:341px;height:91px;border:1px solid var(--line);border-radius:46px;background:linear-gradient(180deg,#f7f7f7,var(--pill-bg));padding:10px 30px 0 32px}
.sub-row{display:flex;align-items:center;height:30px;margin-bottom:7px}
.sub-row a{font-size:12.5px;font-weight:500;color:var(--ink);text-decoration:none;letter-spacing:.3px;margin-right:39px;white-space:nowrap}
.sub-row.second{padding-left:16px}
.sub-row a.active{background:linear-gradient(180deg,var(--gold-light),var(--gold));color:#fff;border-radius:15px;padding:8px 16px}

/* content */
.section-head{top:472px;display:flex;align-items:center;gap:22px}
.section-icon{width:50px;height:36px;border-radius:50%;background:linear-gradient(150deg,var(--gold-light),var(--gold))}
.section-head h2{font-size:24px;font-weight:400;color:var(--ink);letter-spacing:.3px}
.section-head h2 em{font-style:normal;color:var(--gold)}
.content{top:525px;width:580px;right:auto}
.lead{font-size:16.5px;line-height:23.5px;color:var(--ink);margin-bottom:9px}
.body-copy{font-size:13.8px;line-height:23.5px;font-weight:300;color:var(--text);margin-bottom:8px}
.features{list-style:none}
.features li{position:relative;padding-left:22px;font-size:13.8px;line-height:23.5px;font-weight:300;margin-bottom:8px}
.features li strong{font-weight:400;color:var(--ink)}
.features li svg{position:absolute;left:0;top:5px}
.photo{position:absolute;left:671px;top:482px;width:434px;height:290px;background:linear-gradient(160deg,#8a8478 0%,#4a4034 45%,#1e1a16 100%)}

/* footer */
.site-footer{position:absolute;left:0;right:0;top:1019px;height:181px;background:var(--footer)}
.foot-nav{position:absolute;left:73px;top:60px;display:flex;gap:29px}
.foot-nav a{color:#fff;font-size:12.5px;font-weight:500;text-decoration:none;letter-spacing:.3px}
.legal{position:absolute;left:73px;top:100px;font-size:12px;line-height:21px;color:var(--footer-text);letter-spacing:.3px}
.foot-brand{position:absolute;right:72px;top:48px;text-align:center}
.foot-brand .brand-mark{width:56px;height:56px;background:#6d6d6d;margin-bottom:10px}
.foot-brand .brand-name{color:#6d6d6d;font-size:16px}
</style>
</head>
<body>
<header class="site-header">
  <div class="follow"><span>FOLLOW US</span>
    <i class="social s1"></i><i class="social s2"></i><i class="social s3"></i><i class="social s4"></i><i class="social s5"></i>
  </div>
  <div class="brand"><div class="brand-mark"></div><div class="brand-name">HARBOR OF MOMENTUM</div></div>
  <a class="cta">REGISTER NOW</a>
</header>

<nav class="main-nav">
  <a>HOME</a><a>ABOUT</a><a class="active">CONFERENCE</a><a>REGISTER</a><a>TESTIMONIALS</a><a>Y FACTOR</a><a>VIDEOS</a><a>CONTACT</a>
</nav>

<div class="wrap breadcrumb">HOME &nbsp;»&nbsp; <span class="current">CONFERENCE</span></div>
<div class="wrap rule"></div>
<h1 class="wrap page-title">6TH ANNUAL NATIONAL CONFERENCE</h1>

<nav class="wrap sub-nav">
  <div class="sub-row"><a class="active">CONFERENCE</a><a>SCHEDULE</a><a>KEYNOTE SPEAKERS</a><a>INDUSTRY EXPERTS</a><a>WORKSHOP PRESENTERS</a><a>CAREER PANEL EXPERTS</a></div>
  <div class="sub-row second"><a>EXECUTIVE LEADERSHIP SESSIONS</a><a>WORKSHOP SESSIONS</a><a>CAREER PANEL SESSIONS</a><a>TRAVEL/HOTEL ACCOMMODATIONS</a><a>SPECIAL EVENTS</a></div>
</nav>

<div class="wrap section-head"><span class="section-icon"></span><h2>OUR <em>CONFERENCE</em></h2></div>

<main class="wrap content">
  <p class="lead">The 6th Annual Harbor Of Momentum Leadership Summit Is Scheduled To Take Place On The Campus Of Bayview State University, Eastridge Hills From Friday, November 21, 2015 – Sunday, November 23, 2015.</p>
  <p class="body-copy">This Incredible Leadership Experience Will Not Only Connect Student Leaders From All Across The Country With An Incredible Diverse Leadership Network Of Students And Professionals That Will Provide Them With The Inspiration, Leadership Development Training, And Professional Skills Needed To Take Their Personal And Leadership Experience To The Next Level, But It's A Life Changing Conference That Consists Of...</p>
  <ul class="features">
    <li><svg width="13" height="13" viewBox="0 0 13 13"><circle cx="6.5" cy="6.5" r="5.5" fill="none" stroke="#b8913f" stroke-width="1.5"/><path d="M4 6.5h4.5M6.5 4.2l2.3 2.3-2.3 2.3" fill="none" stroke="#b8913f" stroke-width="1.4"/></svg><strong>Dynamic</strong> keynote speakers</li>
    <li><svg width="13" height="13" viewBox="0 0 13 13"><circle cx="6.5" cy="6.5" r="5.5" fill="none" stroke="#b8913f" stroke-width="1.5"/><path d="M4 6.5h4.5M6.5 4.2l2.3 2.3-2.3 2.3" fill="none" stroke="#b8913f" stroke-width="1.4"/></svg><strong>Scholarly</strong> workshop sessions on leadership development for student leaders</li>
    <li><svg width="13" height="13" viewBox="0 0 13 13"><circle cx="6.5" cy="6.5" r="5.5" fill="none" stroke="#b8913f" stroke-width="1.5"/><path d="M4 6.5h4.5M6.5 4.2l2.3 2.3-2.3 2.3" fill="none" stroke="#b8913f" stroke-width="1.4"/></svg><strong>Experts</strong> with real-world leadership experience from more than 70 different<br>Summit 500 companies</li>
    <li><svg width="13" height="13" viewBox="0 0 13 13"><circle cx="6.5" cy="6.5" r="5.5" fill="none" stroke="#b8913f" stroke-width="1.5"/><path d="M4 6.5h4.5M6.5 4.2l2.3 2.3-2.3 2.3" fill="none" stroke="#b8913f" stroke-width="1.4"/></svg><strong>Reflection</strong>, Assessment, and Group Activities with Trained Student Affair Professionals</li>
    <li><svg width="13" height="13" viewBox="0 0 13 13"><circle cx="6.5" cy="6.5" r="5.5" fill="none" stroke="#b8913f" stroke-width="1.5"/><path d="M4 6.5h4.5M6.5 4.2l2.3 2.3-2.3 2.3" fill="none" stroke="#b8913f" stroke-width="1.4"/></svg><strong>Tons</strong> of Networking Opportunities with Students and Executives Passionate<br>about Leadership</li>
    <li><svg width="13" height="13" viewBox="0 0 13 13"><circle cx="6.5" cy="6.5" r="5.5" fill="none" stroke="#b8913f" stroke-width="1.5"/><path d="M4 6.5h4.5M6.5 4.2l2.3 2.3-2.3 2.3" fill="none" stroke="#b8913f" stroke-width="1.4"/></svg><strong>Impactful</strong> Service Project that teaches the importance of Service and Civic Engagement</li>
  </ul>
</main>

<div class="photo" role="img" aria-label="Photo of a speaker addressing a seated audience of student leaders in a conference hall"></div>

<footer class="site-footer">
  <nav class="foot-nav"><a>HOME</a><a>ABOUT</a><a>CONFERENCE</a><a>REGISTER</a><a>TESTIMONIALS</a><a>Y FACTOR</a><a>VIDEOS</a><a>CONTACT</a></nav>
  <div class="legal">Copyright © 2015. Company Name All Right Reserved<br>Privacy Policy &nbsp;|&nbsp; Term &amp; Conditions</div>
  <div class="foot-brand"><div class="brand-mark"></div><div class="brand-name">HARBOR OF MOMENTUM</div></div>
</footer>
</body>
</html>
```